Business Cards for a law firm

Business cards for our law firm. Use our silhoette logo and OAK PARTNERS - check our website (www.oakpartners.example)

Contact Information for Business Card

our silhouette logo, OAK PARTNERS, 800-555-0147, Dorian Pemberton, dorian@oakpartners.example

Requirements
Must have
• our silhouette logo, OAK PARTNERS, 800-555-0147, Dorian Pemberton, dorian@oakpartners.example

```html
<!DOCTYPE html>
<html lang="en">
<head>
<meta charset="utf-8">
<title>Oak Partners – Business Cards</title>
<link href="https://fonts.googleapis.com/css2?family=PT+Sans:wght@400;700&display=swap" rel="stylesheet">
<style>
  :root {
    --backdrop: #e5e5e5;
    --card: #000000;
    --accent: #ff6a00;
    --ink: #ffffff;
  }
  * { margin: 0; padding: 0; box-sizing: border-box; }
  html, body {
    width: 1200px;
    height: 1200px;
    overflow: hidden;
    background: var(--backdrop);
  }
  .canvas {
    position: relative;
    width: 1200px;
    height: 1200px;
  }
  .card {
    position: absolute;
    left: 205px;
    width: 790px;
    height: 451px;
    background: var(--card);
    border-radius: 56px;
    overflow: hidden;
  }
  .card--front { top: 129px; }
  .card--back { top: 620px; }

  .card__frame {
    position: absolute;
    inset: 0;
  }

  .holder-name {
    position: absolute;
    left: 43px;
    top: 126px;
    font-family: "PT Sans", sans-serif;
    font-weight: 700;
    font-size: 54px;
    line-height: 1;
    color: var(--ink);
    white-space: nowrap;
  }
  .holder-name__first { color: var(--accent); }

  .contact-list {
    position: absolute;
    left: 43px;
    top: 236px;
    list-style: none;
  }
  .contact-item {
    position: absolute;
    left: 0;
    display: flex;
    align-items: center;
    height: 28px;
    white-space: nowrap;
  }
  .contact-item--phone { top: 0; }
  .contact-item--email { top: 37px; }
  .contact-item--web { top: 77px; }
  .contact-item--address { top: 122px; }

  .contact-item__icon {
    width: 28px;
    height: 28px;
    flex: none;
  }
  .contact-item__divider {
    width: 2px;
    height: 28px;
    background: var(--accent);
    margin: 0 13px 0 8px;
    flex: none;
  }
  .contact-item__text {
    font-family: "PT Sans", sans-serif;
    font-size: 20px;
    color: var(--ink);
    letter-spacing: 0.3px;
  }

  .brand {
    position: absolute;
    left: 135px;
    top: 168px;
    height: 76px;
    display: flex;
    align-items: center;
    gap: 24px;
  }
  .brand__mark {
    width: 64px;
    height: 64px;
    background: var(--ink);
    flex: none;
  }
  .brand__name {
    font-family: "PT Sans", sans-serif;
    font-weight: 700;
    font-size: 50px;
    line-height: 1;
    letter-spacing: 3px;
    color: var(--ink);
    white-space: nowrap;
  }
</style>
</head>
<body>
<main class="canvas">

  <section class="card card--front" aria-label="Business card front">
    <svg class="card__frame" width="790" height="451" viewBox="0 0 790 451" aria-hidden="true">
      <g fill="none" stroke="#ff6a00" stroke-width="15">
        <line x1="617" y1="0" x2="617" y2="100"/>
        <line x1="617" y1="350" x2="617" y2="451"/>
        <polygon points="617,100 726,161 726,290 617,350 507,290 507,161" stroke-linejoin="miter"/>
      </g>
    </svg>

    <h1 class="holder-name"><span class="holder-name__first">Dorian</span> Pemberton</h1>

    <ul class="contact-list">
      <li class="contact-item contact-item--phone">
        <svg class="contact-item__icon" viewBox="0 0 28 28" aria-hidden="true">
          <path d="M6 3 L10 8 L7.5 11 C9 15 13 19 17 20.5 L20 18 L25 22 L23 26 C13 25 3 15 2 5 Z" fill="#ff6a00"/>
        </svg>
        <span class="contact-item__divider"></span>
        <span class="contact-item__text">800-555-0147</span>
      </li>
      <li class="contact-item contact-item--email">
        <svg class="contact-item__icon" viewBox="0 0 28 28" aria-hidden="true">
          <rect x="1.5" y="5" width="25" height="18" rx="2.5" fill="none" stroke="#ff6a00" stroke-width="2.2"/>
          <path d="M4 7 L14 16 L24 7" fill="none" stroke="#ff6a00" stroke-width="2.2"/>
        </svg>
        <span class="contact-item__divider"></span>
        <span class="contact-item__text">dorian@oakpartners.example</span>
      </li>
      <li class="contact-item contact-item--web">
        <svg class="contact-item__icon" viewBox="0 0 28 28" aria-hidden="true">
          <g fill="none" stroke="#ff6a00" stroke-width="1.8">
            <circle cx="14" cy="14" r="12"/>
            <ellipse cx="14" cy="14" rx="5.5" ry="12"/>
            <line x1="14" y1="2" x2="14" y2="26"/>
            <line x1="2" y1="14" x2="26" y2="14"/>
            <path d="M4 8 H24 M4 20 H24"/>
          </g>
        </svg>
        <span class="contact-item__divider"></span>
        <span class="contact-item__text">www.oakpartners.example</span>
      </li>
      <li class="contact-item contact-item--address">
        <svg class="contact-item__icon" viewBox="0 0 28 28" aria-hidden="true">
          <path d="M14 1 C8 1 4 5 4 10.5 C4 14 7 19 14 28 C21 19 24 14 24 10.5 C24 5 20 1 14 1 Z M14 6 A4.5 4.5 0 1 1 13.99 6 Z" fill="#ff6a00" fill-rule="evenodd"/>
        </svg>
        <span class="contact-item__divider"></span>
        <span class="contact-item__text">Your Street,City,State,Pin Code,Country</span>
      </li>
    </ul>
  </section>

  <section class="card card--back" aria-label="Business card back">
    <svg class="card__frame" width="790" height="451" viewBox="0 0 790 451" aria-hidden="true">
      <rect x="0" y="220" width="95" height="13" fill="#ff6a00"/>
      <rect x="695" y="220" width="95" height="13" fill="#ff6a00"/>
    </svg>
    <div class="brand">
      <span class="brand__mark" role="img" aria-label="Firm silhouette logo"></span>
      <p class="brand__name">OAK PARTNERS</p>
    </div>
  </section>

</main>
</body>
</html>
```